Brenlow Estates Website and Logo Design

We need a new logo and website designed for 'Brenlow Estates Ltd', which is a well established Guernsey property holding company founded in 1934.

The company does not currently have a website. The new website should be similar in style and layout to https://www.quorvanhall.example/.

Target Market(s)

Industry, Media, Tenants

Industry/Entity Type

Property Management

Logo Text

BEL OR Brenlow Estates Ltd OR BE

Coding

Coded - Design and coding required

Number of Pages Required

4 page

Font styles to use
Other font styles liked:
• Helvetica

Requirements
Must have
• The logo laying over the picture (like https://www.quorvanhall.example/).
• Big pictures on homepage (like https://www.quorvanhall.example/)

```html
<!DOCTYPE html>
<html lang="en">
<head>
<meta charset="utf-8">
<title>Brenlow Estates Ltd</title>
<link rel="stylesheet" href="https://fonts.googleapis.com/css2?family=Libre+Baskerville:ital,wght@0,400;0,700;1,400&family=Open+Sans:wght@400;600;700&display=swap">
<style>
:root{
  --blue:#1f8fe0;
  --blue-dark:#1677c4;
  --ink:#333;
  --muted:#666;
  --line:#cfd6dc;
  --sea-top:#2b4a66;
  --sea-bottom:#1d2e3e;
  --footer:#1e2a36;
  --white:#fff;
  --page:#fff;
}
*{box-sizing:border-box;margin:0;padding:0}
html,body{width:1200px;height:2280px;overflow:hidden}
body{background:var(--page);font-family:"Open Sans",Helvetica,Arial,sans-serif;color:var(--ink);position:relative}
.hero{position:absolute;left:0;top:0;width:1200px;height:480px;background:linear-gradient(180deg,#4a6a86 0%,var(--sea-top) 45%,var(--sea-bottom) 100%);color:var(--white)}
.hero-photo{position:absolute;inset:0;background:linear-gradient(180deg,rgba(130,160,190,.35),rgba(20,35,50,.55))}
.nav{position:absolute;left:0;top:0;width:100%;height:72px;display:flex;align-items:center;justify-content:space-between;padding:0 60px}
.brand{font-family:"Libre Baskerville",serif;font-size:22px;font-weight:700;color:var(--white)}
.nav-links{display:flex;gap:36px;list-style:none;font-size:14px}
.nav-links li{color:var(--white)}
.hero-copy{position:absolute;left:0;top:190px;width:100%;text-align:center}
.hero-kicker{font-family:"Libre Baskerville",serif;font-style:italic;font-size:28px}
.hero-title{font-size:40px;font-weight:400;line-height:1.2;margin-top:8px}
.btn{display:inline-block;margin-top:30px;background:var(--blue);color:var(--white);font-size:15px;padding:12px 32px;border-radius:3px}
.hero-arrows{position:absolute;top:430px;left:0;width:100%;display:flex;justify-content:center;gap:14px}
.hero-arrows svg{width:28px;height:28px}
.intro{position:absolute;left:160px;top:505px;width:880px}
.intro section+section{margin-top:22px}
.section-title{font-family:"Libre Baskerville",serif;font-size:24px;font-weight:700;text-align:center;color:var(--ink);line-height:1.3}
.section-title em{font-weight:400}
.rule{width:60px;height:2px;background:var(--blue);margin:10px auto 16px}
.copy{font-size:12px;line-height:1.7;color:var(--muted);text-align:center;margin-bottom:8px}
.timeline{position:absolute;left:0;top:985px;width:1200px;height:930px}
.spine{position:absolute;left:599px;top:0;width:2px;height:930px;background:var(--line)}
.marker{position:absolute;left:592px;width:16px;height:16px;border-radius:50%;background:var(--white);border:3px solid var(--blue)}
.era{position:absolute;font-family:"Libre Baskerville",serif;font-style:italic;font-size:17px;color:var(--ink);line-height:24px}
.photo{position:absolute;border-radius:2px}
.photo.cliffs{background:linear-gradient(180deg,#8fb0cf 0%,#7b8f72 45%,#3f5a6e 100%)}
.photo.harbour{background:linear-gradient(180deg,#a9c8e8 0%,#6f95b8 50%,#355a78 100%)}
.photo.town{background:linear-gradient(180deg,#9ab6d4 0%,#b8a890 45%,#4f6f86 100%)}
.entry{position:absolute;width:500px}
.entry p{font-size:12px;line-height:1.75;color:var(--muted);margin-bottom:12px}
.more{font-size:12px;font-weight:700;color:var(--ink);letter-spacing:.5px}
.more span{color:var(--blue)}
.top-btn{position:absolute;left:560px;top:1935px;width:80px;height:36px;background:var(--blue);color:var(--white);font-family:"Libre Baskerville",serif;font-style:italic;font-size:16px;text-align:center;line-height:36px;border-radius:2px}
.contact-bar{position:absolute;left:140px;top:2010px;width:920px;height:44px;background:var(--blue);display:flex;justify-content:center;gap:80px;align-items:center;color:var(--white);font-size:13px;z-index:2}
.contact-bar span{display:flex;align-items:center;gap:8px}
.footer{position:absolute;left:0;top:2032px;width:1200px;height:248px;background:var(--footer);color:#c9d2db}
.footer-links{display:flex;justify-content:center;gap:34px;list-style:none;font-size:13px;margin-top:60px;color:var(--white)}
.socials{display:flex;justify-content:center;gap:10px;margin-top:22px}
.socials i{width:26px;height:26px;background:var(--blue-dark);border-radius:3px;display:block}
.legal{text-align:center;font-size:11px;margin-top:22px;color:#8d99a6}
</style>
</head>
<body>
<header class="hero">
  <div class="hero-photo" role="img" aria-label="Harbour at dusk with moored boats and waterfront buildings"></div>
  <nav class="nav">
    <div class="brand">Brenlow Estates Ltd</div>
    <ul class="nav-links"><li>Home</li><li>About Us</li><li>Services</li><li>Blog</li><li>Contact Us</li></ul>
  </nav>
  <div class="hero-copy">
    <div class="hero-kicker">Brenlow Estates Ltd (BEL)</div>
    <h1 class="hero-title">is a family-owned Guernsey property<br>holding company</h1>
    <span class="btn">Get Started Now</span>
  </div>
  <div class="hero-arrows">
    <svg viewBox="0 0 30 30"><circle cx="15" cy="15" r="14" fill="rgba(255,255,255,.2)"/><path d="M17 9l-6 6 6 6" stroke="#fff" stroke-width="2" fill="none"/></svg>
    <svg viewBox="0 0 30 30"><circle cx="15" cy="15" r="14" fill="rgba(255,255,255,.2)"/><path d="M13 9l6 6-6 6" stroke="#fff" stroke-width="2" fill="none"/></svg>
  </div>
</header>

<div class="intro">
  <section class="welcome">
    <h2 class="section-title">Welcome to <em>Brenlow Estates Ltd</em></h2>
    <div class="rule"></div>
    <p class="copy">Brenlow Estates Ltd (BEL) is a family owned Guernsey property holding company. It has purchased properties that are considered to have potential for development either through refurbishment or new building and has obtained permission to change its residential use to office, retail or industrial use over the years, acquiring an adjacent property on one occasion.</p>
    <p class="copy">BEL's approach as a landlord has always been one of steady, careful stewardship, working with tenants over the long term to keep its buildings in good order and to maximise the quality of each premises.</p>
    <p class="copy">There is no capital gains tax on the island, and the company follows a long-term investment strategy.</p>
  </section>

  <section class="why">
    <h2 class="section-title">Why Guernsey?</h2>
    <div class="rule"></div>
    <p class="copy">The Bailiwick of Guernsey is a British Crown dependency in the English Channel. Its steady government, independent legal system and modest tax regime have made it a welcome home for business for many decades. Consequently, since the 1960s the island's development as an ideal financial centre has drawn international firms and a skilled workforce. The island now enjoys a strong local economy, a thriving property market and a high quality of life, while still retaining its distinctive heritage. Many companies seek local premises, and BEL is well placed to meet that demand with carefully managed commercial and residential space.</p>
  </section>
</div>

<section class="timeline">
  <div class="spine"></div>

  <div class="marker" style="top:4px"></div>
  <div class="era" style="left:628px;top:0">Yesterday</div>
  <div class="photo cliffs" style="left:60px;top:20px;width:520px;height:280px" role="img" aria-label="Rocky coastline with cliffs and sea"></div>
  <div class="entry" style="left:628px;top:40px">
    <p>BEL was founded in 1934 by William Brenlow to manage both his own substantial investments and the property portfolio of his family. The company portfolio consisted of family properties and covered approximately 45,000 sq ft, which are occupied by offices, shops and homes.</p>
    <p>Despite the economic upheaval of the war and the changes that followed, the company held its course, growing slowly and prudently while keeping a close relationship with every tenant.</p>
    <div class="more">READ MORE <span>›</span></div>
  </div>

  <div class="marker" style="top:334px"></div>
  <div class="era" style="left:480px;top:330px;width:96px;text-align:right">Today</div>
  <div class="entry" style="left:60px;top:370px">
    <p>The Brenlow family has built on the foundations laid down by the founder, and each generation has developed and managed the company's holdings further. The portfolio now includes offices, shops and homes across the island, all kept to a high standard.</p>
    <p>Brenlow is proud to work with local tradespeople and partners, and the company continues to invest in sound, well-located buildings that serve the community.</p>
    <div class="more">READ MORE <span>›</span></div>
  </div>
  <div class="photo harbour" style="left:620px;top:340px;width:520px;height:240px" role="img" aria-label="Boats moored in a calm harbour"></div>

  <div class="marker" style="top:644px"></div>
  <div class="era" style="left:628px;top:640px">Tomorrow</div>
  <div class="photo town" style="left:60px;top:630px;width:520px;height:240px" role="img" aria-label="Harbour town waterfront with houses on the hillside"></div>
  <div class="entry" style="left:628px;top:680px">
    <p>In keeping with its past project development philosophy, BEL will continue to look for sound properties with potential and to add value through careful refurbishment. The next generation of the Brenlow family is already involved in the business.</p>
    <p>The company looks forward to serving its tenants and the island for many years to come.</p>
    <div class="more">READ MORE <span>›</span></div>
  </div>
</section>

<div class="top-btn">Top</div>

<div class="contact-bar">
  <span><svg width="14" height="14" viewBox="0 0 14 14"><path d="M3 1l2 3-1 1.5c.8 1.6 2 2.8 3.5 3.5L9 8l3 2-1 2.5C6 12 2 8 1.5 3z" fill="#fff"/></svg>+44 1481 555 0190 - Guernsey office</span>
  <span><svg width="16" height="12" viewBox="0 0 16 12"><rect x=".5" y=".5" width="15" height="11" fill="none" stroke="#fff"/><path d="M1 1l7 6 7-6" stroke="#fff" fill="none"/></svg>Email: hello@brenlowestates.example</span>
</div>

<footer class="footer">
  <ul class="footer-links"><li>Home</li><li>About Us</li><li>Services</li><li>Blog</li><li>Contact Us</li></ul>
  <div class="socials"><i></i><i></i><i></i><i></i></div>
  <p class="legal">© 2024 Brenlow Estates Ltd | All Rights Reserved</p>
</footer>
</body>
</html>
```